redesign of my existing custom website into Wordpress based website

I need someone to redesign my current website into something more classy, simplistic, modern and on trend. I would like it set up on Wordpress in a way thats easy for me to make my own additions to blogs/price changes and promotion banners. I will also need a page that is password protected so members can login and have access to all my training videos and resources.
website is www.tidewellmamas.com.au

Target Market(s)

new mums

Industry/Entity Type

Fitness

Coding

Coded - Design and coding required

Number of Pages Required

5+ page

Colors
33a6d7

Requirements
Must have
• chic, modern, stylish and simplistic.
• a call to action above the page fold
• mobile friendly conversion
• a pop up message as soon as someone enters my sight offering my free report
• a members page that is password protected containing 3 youtube videos and 6 pdf attachments as resources
• a home page
• a contact us page
• an about us page
• a blog page
• a store page
Nice to have
• some examples of my peers websites that I like:
• www.norapellwick.com
• https://www.9qlr.com
• https://41bytedgarth.com
Should not have
• anything gimmicky

```html
<!DOCTYPE html>
<html lang="en">
<head>
<meta charset="utf-8">
<title>About Us – Tidewell Mamas</title>
<link href="https://fonts.googleapis.com/css2?family=Lato:wght@400;700&family=Open+Sans:wght@400;600&display=swap" rel="stylesheet">
<style>
:root{
  --brand:#33a6d7;
  --ink:#333333;
  --body:#666666;
  --muted:#888888;
  --rule:#d6d6d6;
  --white:#ffffff;
}
*{margin:0;padding:0;box-sizing:border-box}
html,body{width:794px;height:1200px;overflow:hidden;background:var(--white)}
body{position:relative;font-family:"Open Sans",sans-serif;color:var(--body)}
.top-bar{position:absolute;left:0;top:0;width:794px;height:2px;background:var(--brand)}
.site-header{position:absolute;left:0;top:2px;width:794px;height:59px}
.brand{position:absolute;left:84px;top:18px;display:flex;align-items:center;gap:6px;font-family:"Lato",sans-serif;font-weight:700;font-size:13px;color:var(--ink)}
.brand-dot{width:22px;height:22px;border:2px solid var(--ink);border-radius:50%}
.main-nav{position:absolute;left:243px;top:25px;display:flex;gap:0;font-family:"Lato",sans-serif;font-size:10px;color:var(--ink)}
.main-nav span{margin-right:28px}
.main-nav span:nth-child(2){margin-right:28px}
.main-nav .active{color:var(--brand)}
.cart{position:absolute;left:638px;top:17px;width:28px;height:28px;border:1px solid #bbb;border-radius:50%;display:flex;align-items:center;justify-content:center}
.login{position:absolute;left:683px;top:25px;font-family:"Lato",sans-serif;font-size:11px;color:var(--ink);display:flex;align-items:center;gap:5px}
.hero{position:absolute;left:0;top:61px;width:794px;height:208px;background:linear-gradient(100deg,#3a3535 0%,#5a4a48 30%,#b0507a 50%,#4a3f45 70%,#2f2b2d 100%)}
.hero-title{position:absolute;left:0;top:80px;width:794px;text-align:center;font-family:"Lato",sans-serif;font-weight:700;font-size:42px;color:var(--white);letter-spacing:0.5px}
.hero-arrow{position:absolute;top:90px}
.breadcrumb{position:absolute;left:65px;top:289px;font-family:"Lato",sans-serif;font-size:10px;color:var(--ink)}
.breadcrumb .current{color:var(--brand)}
.divider{position:absolute;left:65px;width:664px;height:1px;background:var(--rule)}
.portrait{position:absolute;left:65px;top:349px;width:228px;height:284px;background:linear-gradient(180deg,#8a8078 0%,#b9c96a 55%,#3a3a3a 100%)}
.copy{position:absolute;font-size:7.4px;line-height:17px;color:var(--body)}
.copy p{margin-bottom:17px}
.copy-side{left:322px;top:344px;width:408px}
.copy-full{left:65px;top:656px;width:665px}
.pitch{position:absolute;left:65px;top:861px;font-size:10px;line-height:21px;color:#444;font-weight:600}
.btn{position:absolute;left:65px;top:917px;width:107px;height:25px;border-radius:13px;background:var(--brand);color:var(--white);font-family:"Lato",sans-serif;font-weight:700;font-size:8.5px;display:flex;align-items:center;justify-content:center}
.footer-line{position:absolute;left:0;top:988px;width:794px;height:3px;background:var(--brand)}
.footer-brand{position:absolute;left:66px;top:1062px;display:flex;align-items:center;gap:8px;font-family:"Lato",sans-serif;font-weight:700;font-size:16px;color:var(--ink)}
.footer-brand .brand-dot{width:30px;height:30px}
.col-title{position:absolute;top:1021px;font-family:"Lato",sans-serif;font-size:13px;color:var(--ink)}
.links{position:absolute;left:253px;top:1047px;font-size:7.5px;line-height:15.3px;color:var(--body);list-style:none}
.sub-text{position:absolute;left:367px;top:1047px;width:190px;font-size:7.5px;line-height:15.3px}
.email{position:absolute;left:367px;top:1103px;width:108px;height:24px;border:1px solid #ccc;border-right:none;font-size:7.5px;color:#aaa;padding:7px 8px}
.sub-btn{position:absolute;left:475px;top:1103px;width:60px;height:24px;background:var(--brand);color:var(--white);font-family:"Lato",sans-serif;font-weight:700;font-size:8px;display:flex;align-items:center;justify-content:center}
.social{position:absolute;left:592px;top:1051px;list-style:none;font-size:7.5px}
.social li{display:flex;align-items:center;gap:12px;height:20px;margin-bottom:13px}
.social i{width:20px;height:20px;background:#9a9a9a;border-radius:3px;display:block}
.copyright{position:absolute;left:0;top:1171px;width:794px;text-align:center;font-size:7.5px;color:var(--body)}
</style>
</head>
<body>
<div class="top-bar"></div>
<header class="site-header">
  <div class="brand"><span class="brand-dot"></span>Tidewell Mamas</div>
  <nav class="main-nav"><span>HOME</span><span class="active">ABOUT US</span><span>PROGRAM</span><span>BLOG</span><span>SHOP</span><span>CONTACT US</span></nav>
  <div class="cart"><svg width="14" height="12" viewBox="0 0 14 12"><path d="M0 1h2.5l2 7h7l1.5-5H4" fill="none" stroke="#33a6d7" stroke-width="1.6"/><circle cx="5.5" cy="10.5" r="1.2" fill="#33a6d7"/><circle cx="10.5" cy="10.5" r="1.2" fill="#33a6d7"/></svg></div>
  <div class="login"><svg width="8" height="10" viewBox="0 0 8 10"><path d="M2 4V3a2 2 0 0 1 4 0v1" fill="none" stroke="#33a6d7" stroke-width="1.4"/><rect x="0" y="4" width="8" height="6" rx="1" fill="#33a6d7"/></svg>LOGIN</div>
</header>

<section class="hero" role="img" aria-label="Mum doing a floor crunch workout in a living room">
  <svg class="hero-arrow" style="left:24px" width="14" height="28" viewBox="0 0 14 28"><path d="M12 2L2 14l10 12" fill="none" stroke="#bbb" stroke-width="2.5"/></svg>
  <h1 class="hero-title">ABOUT US</h1>
  <svg class="hero-arrow" style="left:756px" width="14" height="28" viewBox="0 0 14 28"><path d="M2 2l10 12L2 26" fill="none" stroke="#bbb" stroke-width="2.5"/></svg>
</section>

<div class="breadcrumb">HOME &nbsp;&gt;&gt;&nbsp; <span class="current">ABOUT US</span></div>
<div class="divider" style="top:314px"></div>

<div class="portrait" role="img" aria-label="Portrait of the trainer sitting on the floor in a lime top"></div>

<div class="copy copy-side">
  <p>After a life time of competitive sports and as a qualified personal trainer, I thought I knew exactly what it would take to get back into shape after having babies. I put on a massive 30 kgs with my first pregnancy and found myself in a situation for the first time in my life where I had to lose a lot of weight. I thought the answer was just to keep training and eating the way I always did before babies, little did I know this wasn't the best way at all. I struggled with losing the weight and I also struggled with a lot of back pain and with abdominal separation that wouldn't fix itself.</p>
  <p>From here i spent a lot of time and energy studying post pregnancy training and found I was doing it all wrong. I totally underestimated the power of core strength and the benefit of easing yourself back into training with the correct post pregnancy specific exercises. I also found my diet was all wrong for someone trying to lose weight with way too much allocation to starchy high GI carbs on my plate and not enough veggies and proteins.</p>
  <p>After my second pregnancy I was so excited to trial out some of my new found knowledge to see how it would go as once again I found myself in a situation of putting on another 25kg. Pleasingly I was able to not only bounce back into shape a lot quicker this time, most importantly I was able to do so without any back pain and my separation also fixed itself within just a few months.</p>
</div>

<div class="copy copy-full">
  <p>This is how I came to create the 12 Week Home Workout Program For Mums. I put pen to paper and wrote down all the training routines I used to get back into shape after my second baby. I then tested it out on other mums to make sure it worked for others too and all of the mums I tested on lost at least 18cms across their body doing the program. I also used this exact same program post baby number 3 and at the end of the 12 week program I was fitter and healthier than I had ever been.</p>
  <p>Of course it wasn't just the exercise that helped, it was also a commitment to a healthy eating plan with portion controlled meals that are full of the right mix of protein, vegetables and healthy carbs. The recipes I have put together as part of this program are on constant rotation in my kitchen, so you will see its possible to eat delicious meals and still lose weight at the same time.</p>
  <p>I firmly believe that you do not need to go on any crazy diets, take any pills or spend hours away from the family sweating it out at the gym to get back into shape after you have babies. All it takes is a bit of commitment to regular, post pregnancy specific exercise and a healthy balanced diet. With this combination you will not only be fitter and healthier than ever, you will also have loads more energy for you and your family and be feeling great within yourself!</p>
</div>

<div class="pitch">It's your turn to take the time to focus on you.<br>Take the first step to being a fitter, healthier more energetic mumma and join my program today!</div>
<div class="btn">GET STARTED NOW</div>

<footer>
  <div class="footer-line"></div>
  <div class="footer-brand"><span class="brand-dot"></span>Tidewell Mamas</div>
  <h3 class="col-title" style="left:253px">Quick Links</h3>
  <ul class="links"><li>Home</li><li>About Us</li><li>Program</li><li>Blog</li><li>Shop</li><li>Contact Us</li></ul>
  <h3 class="col-title" style="left:367px">Subscribe</h3>
  <p class="sub-text">Register your details below and receive tones of free information on fitness and living a healthy lifestyle</p>
  <div class="email">Email Address</div>
  <div class="sub-btn">SUBSCRIBE</div>
  <h3 class="col-title" style="left:591px">Stay Connected</h3>
  <ul class="social"><li><i></i>Friendpage</li><li><i></i>Snapgallery</li><li><i></i>Workline</li></ul>
  <div class="divider" style="top:1155px"></div>
  <p class="copyright">Copyrights © 2017, Tidewell Mamas. All rights reserved.</p>
</footer>
</body>
</html>
```